Construction company business card

One side to be the logo with the company name, The other side I would like: (Tomas verbick) Project manager 41 barrow crescent hallam 52917306224783(03) 9703 2428Info@gudeljgroup.comAnd then maybe a couple dot points saying what we do:Construction (commercial & industrial) Civil construction

Anything else please contact me!
Maybe curved st one edge of the card

Target Market(s)

Older clientele

Industry/Entity Type

Construction Company

Contact Information for Business Card

Read above

Colors
3277b5
1b1b1b
9d9d9d

Requirements
Must have
• Use my logo on one side
Nice to have
• Read above
Should not have
• Read above

```html
<!DOCTYPE html>
<html lang="en">
<head>
<meta charset="utf-8">
<title>Barrowline Construction – Business Card</title>
<link href="https://fonts.googleapis.com/css2?family=Fira+Sans:wght@300;400;600&display=swap" rel="stylesheet">
<style>
  :root {
    --brand-blue: #3277b5;
    --card-dark: #2b2b2b;
    --ink-dark: #1b1b1b;
    --text-light: #d6d3ce;
    --text-muted: #9d9d9d;
    --backdrop: #e6e1da;
  }
  * { margin: 0; padding: 0; box-sizing: border-box; }
  html, body {
    width: 1200px;
    height: 1047px;
    overflow: hidden;
    background: var(--backdrop);
    font-family: "Fira Sans", sans-serif;
  }
  .business-card {
    position: absolute;
    left: 80px;
    top: 241px;
    width: 1040px;
    height: 565px;
    border-radius: 24px;
    background: linear-gradient(135deg, #353535 0%, var(--card-dark) 55%, var(--ink-dark) 100%);
    overflow: hidden;
    color: var(--text-light);
  }
  .company-name {
    position: absolute;
    left: 51px;
    top: 42px;
    color: var(--brand-blue);
    font-weight: 600;
    text-transform: uppercase;
    line-height: 1;
  }
  .company-name .primary {
    display: block;
    font-size: 40px;
    letter-spacing: 1px;
  }
  .company-name .secondary {
    display: block;
    margin-top: 6px;
    font-size: 15px;
    letter-spacing: 11.2px;
  }
  .person-name {
    position: absolute;
    left: 48px;
    top: 268px;
    font-size: 31px;
    font-weight: 400;
    letter-spacing: 1.5px;
    text-transform: uppercase;
  }
  .person-role {
    position: absolute;
    left: 48px;
    top: 312px;
    font-size: 25px;
    font-weight: 300;
    letter-spacing: 0.8px;
  }
  .address {
    position: absolute;
    left: 48px;
    top: 360px;
    font-size: 24px;
    font-weight: 300;
    line-height: 33px;
    letter-spacing: 0.8px;
    font-style: normal;
  }
  .contact-list {
    position: absolute;
    left: 48px;
    top: 440px;
    list-style: none;
    font-size: 24px;
    font-weight: 300;
    letter-spacing: 0.8px;
  }
  .contact-list li {
    display: flex;
    align-items: center;
    height: 34px;
  }
  .contact-list svg {
    width: 16px;
    height: 16px;
    margin-right: 12px;
    fill: none;
    stroke: var(--text-light);
    stroke-width: 1.6;
  }
  .brand-mark {
    position: absolute;
    left: 482px;
    top: 0;
    width: 558px;
    height: 565px;
    display: flex;
    align-items: center;
    justify-content: center;
    gap: 22px;
  }
  .brand-mark .dot {
    width: 56px;
    height: 56px;
    border-radius: 50%;
    background: var(--brand-blue);
  }
  .brand-mark .label {
    color: var(--brand-blue);
    font-size: 64px;
    font-weight: 600;
    letter-spacing: 1px;
    text-transform: uppercase;
  }
</style>
</head>
<body>
  <div class="business-card">
    <div class="company-name">
      <span class="primary">Barrowline</span>
      <span class="secondary">Construction</span>
    </div>

    <h1 class="person-name">Tomas Verbick</h1>
    <p class="person-role">Project manager</p>

    <address class="address">41 barrow crescent<br>elmsvale 5291</address>

    <ul class="contact-list">
      <li>
        <svg viewBox="0 0 16 16" aria-hidden="true"><path d="M4 2 L6.5 5 L5 6.8 C6 9 7 10 9.2 11 L11 9.5 L14 12 L12.5 14 C7 13.5 2.5 9 2 3.5 Z"/></svg>
        73 0622 4783
      </li>
      <li>
        <svg viewBox="0 0 16 16" aria-hidden="true"><rect x="4.5" y="1.5" width="7" height="13" rx="1.2"/><line x1="7" y1="12" x2="9" y2="12"/></svg>
        (03) 9418 6573
      </li>
      <li>
        <svg viewBox="0 0 16 16" aria-hidden="true"><rect x="1.5" y="3.5" width="13" height="9" rx="1"/><path d="M1.5 4 L8 9 L14.5 4"/></svg>
        Info@verbickgroup.com
      </li>
    </ul>

    <div class="brand-mark">
      <span class="dot" aria-hidden="true"></span>
      <span class="label">Barrowline</span>
    </div>
  </div>
</body>
</html>
```